Telecommunications/Power civil contractor needs business card design

Were a new telecommunications/power underground civil contractor that is looking for a new business card design. Our company colours are silver or grey and orange. Feel free to use the white background logo or the black background logo.

Target Market(s)

Local contractors, utility companies, private sector mining/energy companies, developers.

Industry/Entity Type

Telecommunications

Contact Information for Business Card

Each card will need the following info:
Persons name:
Title:
E-mail:
Phone number:
Shop Address:
Mailing Address:

Requirements
Must have
• Each card will need the following info:
• Persons name:
• Title:
• E-mail:
• Phone number:
• Shop Address:
• Mailing Address:

```html
<!DOCTYPE html>
<html lang="en">
<head>
<meta charset="utf-8">
<title>Trenchline Civil Inc – Business Card</title>
<link href="https://fonts.googleapis.com/css2?family=Open+Sans:wght@400;700;800&display=swap" rel="stylesheet">
<style>
  :root {
    --backdrop: #2c2e33;
    --card: #ffffff;
    --orange: #f05a1e;
    --grey: #8a8c8f;
    --text: #4a4a4a;
    --text-light: #5a5a5a;
  }
  * { margin: 0; padding: 0; box-sizing: border-box; }
  html, body {
    width: 1200px;
    height: 864px;
    overflow: hidden;
    background: var(--backdrop);
    font-family: "Open Sans", Arial, sans-serif;
  }
  .canvas {
    position: relative;
    width: 1200px;
    height: 864px;
  }
  .card {
    position: absolute;
    width: 580px;
    height: 331px;
    background: var(--card);
    overflow: hidden;
    box-shadow: 0 10px 24px rgba(0,0,0,0.45);
  }
  .card--front { left: 200px; top: 70px; }
  .card--back  { left: 330px; top: 460px; }

  .person {
    position: absolute;
    left: 48px;
    top: 36px;
  }
  .person__name {
    color: var(--orange);
    font-weight: 700;
    font-size: 19px;
    line-height: 1.2;
  }
  .person__title {
    color: var(--text);
    font-size: 18px;
    line-height: 1.25;
  }
  .address {
    position: absolute;
    left: 48px;
    top: 122px;
    color: var(--text-light);
    font-size: 15px;
    line-height: 1.5;
    font-style: normal;
  }
  .contacts {
    position: absolute;
    left: 48px;
    top: 212px;
    list-style: none;
    color: var(--text-light);
    font-size: 15px;
    line-height: 1.6;
  }
  .contacts li {
    display: flex;
    align-items: center;
    gap: 10px;
  }
  .contacts svg { width: 13px; height: 13px; flex: none; }

  .deco-ring {
    position: absolute;
  }
  .deco-ring--front { right: -130px; top: 56px; width: 260px; height: 260px; }
  .deco-ring--back  { left: -170px; top: -20px; width: 300px; height: 300px; }

  .brand {
    position: absolute;
    right: 44px;
    bottom: 40px;
    display: flex;
    flex-direction: column;
    align-items: center;
    gap: 10px;
  }
  .brand__dot {
    width: 64px;
    height: 64px;
    border-radius: 50%;
    border: 4px solid var(--grey);
  }
  .brand__name {
    color: var(--orange);
    font-weight: 800;
    font-size: 22px;
    letter-spacing: 1px;
    text-transform: uppercase;
  }
</style>
</head>
<body>
<main class="canvas">

  <section class="card card--front" aria-label="Business card front">
    <div class="person">
      <p class="person__name">Marlow Keane</p>
      <p class="person__title">Managing Director</p>
    </div>
    <address class="address">
      24 Ridgeway Road,<br>
      Suite 210, Harlow Falls, WA 55512
    </address>
    <ul class="contacts">
      <li>
        <svg viewBox="0 0 16 16" aria-hidden="true"><path fill="#f05a1e" d="M3 2h3l1.5 3.5L5.6 7a9 9 0 0 0 3.4 3.4l1.5-1.9L14 10v3a1 1 0 0 1-1 1A12 12 0 0 1 2 3a1 1 0 0 1 1-1z"/></svg>
        555.204.318
      </li>
      <li>
        <svg viewBox="0 0 16 16" aria-hidden="true"><rect x="1" y="3" width="14" height="10" rx="1" fill="#f05a1e"/><path d="M1.5 3.8 8 9l6.5-5.2" fill="none" stroke="#fff" stroke-width="1.3"/></svg>
        info@trenchlinecivil.com
      </li>
    </ul>
    <svg class="deco-ring deco-ring--front" viewBox="0 0 260 260" aria-hidden="true">
      <circle cx="130" cy="130" r="122" fill="none" stroke="#f05a1e" stroke-width="8"/>
    </svg>
  </section>

  <section class="card card--back" aria-label="Business card back">
    <svg class="deco-ring deco-ring--back" viewBox="0 0 300 300" aria-hidden="true">
      <circle cx="150" cy="150" r="140" fill="none" stroke="#8a8c8f" stroke-width="10"/>
    </svg>
    <div class="brand">
      <span class="brand__dot" aria-hidden="true"></span>
      <p class="brand__name">Trenchline Civil Inc</p>
    </div>
  </section>

</main>
</body>
</html>
```